1" x 3" label needed for essential oil bottle(s) - new ecommerce company

We need a label designed for 10 ml bottles of essential oils. We are offering 9 different types of essential oil: Lavender, Cedarwood, Eucalyptus, Frankincense, Lemon, Orange, Peppermint, Rosemary, and Tea Tree. The label should have a space for the type of essential oil. The bottles are an amber color (am including a photo) as essential oils are sensitive to light. also am including an AI file of our logo, which we'd like included on the label; the logo file also contains our logo colors, a dark blue and light grey. We'd also like the following on the label: "CAUTION: EYE AND SKIN IRRITANT. Avoid contact with eyes and skin. Wash hands after handling. If eye contact occurs, flush with water for 15 minutes. Not intended for topical or internal use. Contains Essential Oils. KEEP OUT OF REACH OF CHILDREN."
Also "Ingredients: 100% pure essential oil, GC tested."
Also "0.33 fl oz (10 ml)
Finally, we will need to include a sideways bar code on the right side of the label, so need 3/8" of white space on the right of the label.
We'd like the label to be calming, but modern, friendly, and confident.

```html
<!DOCTYPE html>
<html lang="en">
<head>
<meta charset="utf-8">
<title>Solvena Essential Oil Labels</title>
<link rel="stylesheet" href="https://fonts.googleapis.com/css2?family=Marcellus&family=Open+Sans:wght@600;700&display=swap">
<style>
  :root {
    --page: #e3e8e8;
    --paper: #f4f4f2;
    --ink: #3b4a52;
    --brand: #2f4550;
    --stripe: #363b3c;
    --lavender: #9c63f2;
    --lavender-band: #a475f5;
    --eucalyptus: #69a81f;
    --eucalyptus-band: #6bb11c;
    --warn-red: #d5262c;
    --white: #ffffff;
  }
  * { margin: 0; padding: 0; box-sizing: border-box; }
  html, body { width: 1200px; height: 800px; overflow: hidden; }
  body { background: var(--page); position: relative; font-family: "Open Sans", Arial, sans-serif; }

  .label {
    position: absolute; left: 33px; width: 1138px; height: 380px;
    background: var(--paper); overflow: hidden;
  }
  .label--lavender { top: 16px; --accent: var(--lavender); --band: var(--lavender-band); }
  .label--eucalyptus { top: 412px; --accent: var(--eucalyptus); --band: var(--eucalyptus-band); }

  .warning {
    position: absolute; left: 73px; top: 27px; width: 222px; height: 285px;
    border: 2px solid var(--ink); color: var(--ink);
    padding: 10px 8px; text-align: center; font-weight: 700;
    font-size: 12.5px; line-height: 1.3;
  }
  .warning__caution { font-size: 12.5px; margin-bottom: 4px; }
  .warning__body { font-weight: 600; margin-bottom: 12px; }
  .warning__children { display: flex; align-items: flex-start; gap: 6px; text-align: left; margin: 0 0 20px 6px; }
  .warning__children svg { flex: none; width: 24px; height: 24px; }
  .warning__light { font-weight: 600; margin-bottom: 18px; }
  .warning__producer { font-size: 14.5px; line-height: 1.25; }

  .brand-mark {
    position: absolute; left: 536px; top: 40px; width: 64px; height: 64px;
    border: 2.5px solid var(--brand); border-radius: 50%;
  }
  .brand-name {
    position: absolute; left: 380px; width: 376px; top: 130px; text-align: center;
    font-family: "Marcellus", Georgia, serif; font-size: 38px; letter-spacing: 8px;
    color: var(--brand);
  }
  .oil-name {
    position: absolute; left: 340px; width: 456px; top: 192px; text-align: center;
    font-family: "Marcellus", Georgia, serif; font-size: 47px; letter-spacing: 1px;
    color: var(--accent);
  }
  .oil-claim {
    position: absolute; left: 340px; width: 456px; top: 252px; text-align: center;
    font-size: 13px; font-weight: 600; color: #2c2f30; letter-spacing: 0.3px;
  }

  .stripe { position: absolute; left: 0; width: 100%; top: 333px; height: 11px; background: var(--stripe); }
  .band { position: absolute; left: 0; width: 100%; top: 352px; height: 28px; background: var(--band); }
  .volume {
    position: absolute; left: 499px; top: 300px; width: 139px; height: 84px;
    background: var(--accent); border: 5px solid var(--paper); border-bottom: 0;
    border-radius: 12px 12px 0 0; color: var(--white);
    text-align: center; font-weight: 700; font-size: 17.5px; line-height: 1.2; padding-top: 8px;
  }

  .botanical { position: absolute; left: 722px; top: 12px; width: 90px; height: 340px; border-radius: 45px; }
  .label--lavender .botanical { background: linear-gradient(180deg, #7a53c8, #5b3a98 70%, #4a5a3c); }
  .label--eucalyptus .botanical { background: linear-gradient(180deg, #5c9a3a, #2f6a2c 70%, #3d5a34); }

  .barcode-space {
    position: absolute; left: 840px; top: 27px; width: 223px; height: 285px;
    border: 2px solid var(--stripe); background: var(--paper);
  }
</style>
</head>
<body>

  <section class="label label--lavender">
    <div class="warning">
      <p class="warning__caution">"CAUTION: EYE AND SKIN IRRITANT.</p>
      <p class="warning__body">If eye contact occurs, flush with water for 15 minutes. Not for topical or use. Contains Essential Oils.</p>
      <p class="warning__children">
        <svg viewBox="0 0 24 24" aria-hidden="true"><circle cx="12" cy="12" r="10" fill="none" stroke="var(--warn-red)" stroke-width="2.5"/><line x1="5" y1="5" x2="19" y2="19" stroke="var(--warn-red)" stroke-width="2.5"/></svg>
        <span>KEEP OUT OF REACH OF CHILDREN."</span>
      </p>
      <p class="warning__light">OILS ARE SENSITIVE TO LIGHT</p>
      <p class="warning__producer">"PRODUCED BY:<br>SOLVENA INC., BAYSIDE, FL USA"</p>
    </div>
    <div class="brand-mark" aria-hidden="true"></div>
    <p class="brand-name">SOLVENA</p>
    <h2 class="oil-name">LAVENDER</h2>
    <p class="oil-claim">100% PURE ESSENTIAL OIL, GC TESTED</p>
    <div class="botanical" role="img" aria-label="Sprig of lavender flowers"></div>
    <div class="barcode-space"></div>
    <div class="stripe"></div>
    <div class="band"></div>
    <div class="volume">(10 mL)<br>0.33 fl oz</div>
  </section>

  <section class="label label--eucalyptus">
    <div class="warning">
      <p class="warning__caution">"CAUTION: EYE AND SKIN IRRITANT.</p>
      <p class="warning__body">If eye contact occurs, flush with water for 15 minutes. Not for topical or use. Contains Essential Oils.</p>
      <p class="warning__children">
        <svg viewBox="0 0 24 24" aria-hidden="true"><circle cx="12" cy="12" r="10" fill="none" stroke="var(--warn-red)" stroke-width="2.5"/><line x1="5" y1="5" x2="19" y2="19" stroke="var(--warn-red)" stroke-width="2.5"/></svg>
        <span>KEEP OUT OF REACH OF CHILDREN."</span>
      </p>
      <p class="warning__light">OILS ARE SENSITIVE TO LIGHT</p>
      <p class="warning__producer">"PRODUCED BY:<br>SOLVENA INC., BAYSIDE, FL USA"</p>
    </div>
    <div class="brand-mark" aria-hidden="true"></div>
    <p class="brand-name">SOLVENA</p>
    <h2 class="oil-name">EUCALYPTUS</h2>
    <p class="oil-claim">100% PURE ESSENTIAL OIL, GC TESTED</p>
    <div class="botanical" role="img" aria-label="Eucalyptus branch with green leaves"></div>
    <div class="barcode-space"></div>
    <div class="stripe"></div>
    <div class="band"></div>
    <div class="volume">(10 mL)<br>0.33 fl oz</div>
  </section>

</body>
</html>
```